Design a compelling Tarnwove Business Card that will drive people to my site

I want a business card that I can give to people—less to tell them who I am and more to direct them to my website. My website is a portal for Pelmor Aquatics Officials and a place for people who want to become Pelmor Aquatics Officials.
I am uploading my official company logo as well as a business card mockup that I did on my own. Please feel free to completely stray from this design.
I've included a screen recording of the homepage of my website as well.
Target Market(s)
Pelmor Aquatics Officials and people who desire to become one
Contact Information for Business Card
website url
Look and feel
Each slider illustrates characteristics of the customer's brand and the style your logo design should communicate.

```html
<!DOCTYPE html>
<html lang="en">
<head>
<meta charset="utf-8">
<title>Tarnwove Business Card</title>
<link rel="stylesheet" href="https://fonts.googleapis.com/css2?family=Montserrat:wght@500;600;700&display=swap">
<style>
  :root {
    --page-bg: #b9b9b9;
    --brand-blue: #3a55a4;
    --brand-blue-soft: #4763b3;
    --tint-blue: #a9b8e6;
    --paper: #ffffff;
    --card-radius: 22px;
  }
  * { box-sizing: border-box; margin: 0; padding: 0; }
  html, body {
    width: 1200px; height: 802px; overflow: hidden;
    background: var(--page-bg);
    font-family: "Montserrat", sans-serif;
  }
  .stage {
    width: 1200px; height: 802px;
    display: flex; align-items: center; justify-content: center; gap: 40px;
  }
  .card {
    position: relative;
    width: 540px; height: 310px;
    border-radius: var(--card-radius);
    overflow: hidden;
  }
  .card--front { background: var(--paper); }
  .card--back { background: var(--brand-blue); }

  .front-wave { position: absolute; inset: 0; }

  .front-wordmark {
    position: absolute; left: 30px; top: 96px;
    font-weight: 700; font-size: 46px; letter-spacing: -1px;
    color: var(--brand-blue);
  }
  .contact-block {
    position: absolute; left: 32px; top: 192px;
    color: var(--tint-blue);
  }
  .contact-name { font-weight: 600; font-size: 17px; }
  .contact-title { font-weight: 500; font-size: 12px; margin-top: 2px; }
  .contact-rule {
    width: 16px; height: 1px; background: var(--tint-blue);
    margin: 8px 0 6px;
  }
  .contact-list { list-style: none; }
  .contact-list li {
    display: flex; align-items: center; gap: 7px;
    font-size: 12px; font-weight: 500; line-height: 17px;
  }
  .contact-list svg { width: 11px; height: 11px; flex: none; }

  .back-pattern {
    position: absolute; inset: 0;
    background: radial-gradient(circle at 78% 30%, rgba(255,255,255,0.10), transparent 45%),
                radial-gradient(circle at 15% 82%, rgba(255,255,255,0.08), transparent 35%),
                var(--brand-blue);
  }
  .back-wordmark {
    position: absolute; left: 0; right: 0; top: 118px;
    text-align: center;
    font-weight: 700; font-size: 68px; letter-spacing: -1.5px;
    color: var(--paper);
  }
</style>
</head>
<body>
<main class="stage">
  <section class="card card--front" aria-label="Business card front">
    <svg class="front-wave" viewBox="0 0 540 310" aria-hidden="true">
      <path d="M0,178 H250 C310,178 340,150 385,110 C430,70 470,42 540,32 V310 H0 Z" fill="var(--brand-blue)"/>
    </svg>
    <div class="front-wordmark">tarnwove</div>
    <div class="contact-block">
      <p class="contact-name">Marcus Ellery</p>
      <p class="contact-title">CEO &amp; Founder</p>
      <div class="contact-rule"></div>
      <ul class="contact-list">
        <li>
          <svg viewBox="0 0 12 12"><path d="M2.5 1 L4.5 1 L5.2 3.5 L4 4.5 C4.6 6 6 7.4 7.5 8 L8.5 6.8 L11 7.5 V9.5 C11 10.3 10.3 11 9.5 11 C5 11 1 7 1 2.5 C1 1.7 1.7 1 2.5 1 Z" fill="currentColor"/></svg>
          (555) 014-2270
        </li>
        <li>
          <svg viewBox="0 0 12 12"><rect x="1" y="2.5" width="10" height="7" rx="1" fill="currentColor"/><path d="M1.5 3 L6 6.5 L10.5 3" stroke="var(--brand-blue)" stroke-width="1" fill="none"/></svg>
          marcus@tarnwove.com
        </li>
        <li>
          <svg viewBox="0 0 12 12"><circle cx="6" cy="6" r="5" fill="none" stroke="currentColor" stroke-width="1.2"/><path d="M1 6 H11 M6 1 C3.5 3.5 3.5 8.5 6 11 M6 1 C8.5 3.5 8.5 8.5 6 11" stroke="currentColor" stroke-width="0.9" fill="none"/></svg>
          www.tarnwove.com
        </li>
      </ul>
    </div>
  </section>

  <section class="card card--back" aria-label="Business card back">
    <div class="back-pattern" role="img" aria-label="Soft bubble pattern in translucent blue"></div>
    <div class="back-wordmark">tarnwove</div>
  </section>
</main>
</body>
</html>
```